Cutting Edge Property Services Provider is Looking to Update Business Card Design

We are looking to freshen up our business cards to match our cutting edge technology based image.

KORVANEX - Where Care Finds Its Pulse

More information about our company can be found on our website at www.korvanex-demo.net

We integrate technology in a historically low tech industry.

We have appeared on the Brisk 300/3000 list 2 years in a row and we're previously recognized as the 5th Quickest Rising Firm in San Diego.

Our core colors are blue and white, but are not against accents that might improve our image.

We currently have our Mission Statement on our Business Cards in a folding design:
KORVANEX IS THE LEADING BUILDING SERVICES INNOVATOR. BY COMBINING TECHNOLOGY WITH FUNCTIONAL TOOS THAT IMPROVE EFFICIENCY IN THE WORKPLACE, WE PROVIDE UNPARALLELED SERVICE IN THE INDUSTRY. DEVELOPING LASTING RELATIONSHIPS WITH OUR CLIENTS AND ASSOCIATES IS THE CORNERSTONE OF OUR SUCCESS.

We'd like to convey the image of a cutting edge, technology based company. Want the cards to pop.

Target Market(s)

Commercial Property Managers - 20 to 50 year old professionals

Industry/Entity Type

Business

Requirements
Must have
• Must utilize our logo obviously, but are definitely open to using variations on the logo. Utilizing the components of the logo, but maybe in different configurations or backgrounds, etc...

Must use the Name: KORVANEX.
Can also use KORVANEX PROPERTY SERVICES.

Must include the Mission Statement

Must say: Where Care Finds Its Pulse
Nice to have
• We are considering plastic stock, shaped cards, or folding cards.

Nothing over the top or really expensive, but will consider if it conveys innovation and technology.
Should not have
• No images of toilets, buildings, trees, or anything relating to commercial properties.

We want to convey our technology image.

```html
<!DOCTYPE html>
<html lang="en">
<head>
<meta charset="utf-8">
<title>Korvanex Business Card</title>
<link rel="stylesheet" href="https://fonts.googleapis.com/css2?family=Questrial&display=swap">
<style>
  :root {
    --brand-blue: #0b4a76;
    --ink: #2a2a2a;
    --muted: #444444;
    --card: #ffffff;
    --stage: #e7e4e0;
    --divider: #9aa7b2;
  }
  * { margin: 0; padding: 0; box-sizing: border-box; }
  html, body {
    width: 1200px;
    height: 713px;
    overflow: hidden;
  }
  body {
    position: relative;
    background: var(--stage);
    font-family: "Questrial", "Century Gothic", sans-serif;
    color: var(--ink);
  }
  .side-label {
    position: absolute;
    top: 28px;
    width: 200px;
    text-align: center;
    font-size: 23px;
    color: #1c1c1c;
  }
  .side-label--front { left: 222px; }
  .side-label--back { left: 803px; }

  .card {
    position: absolute;
    width: 525px;
    height: 298px;
    background: var(--card);
    border-radius: 22px;
    box-shadow: 0 3px 10px rgba(0,0,0,0.18);
  }
  .card--front-top { left: 55px; top: 72px; }
  .card--front-bottom { left: 55px; top: 372px; }
  .card--back-top { left: 640px; top: 72px; }
  .card--back-bottom { left: 640px; top: 372px; }

  .brand {
    position: absolute;
    left: 0; right: 0;
    display: flex;
    align-items: center;
    justify-content: center;
    gap: 18px;
    color: var(--brand-blue);
    letter-spacing: 0.06em;
  }
  .brand__mark { background: var(--brand-blue); flex: none; }
  .brand--large { top: 112px; font-size: 58px; }
  .brand--large .brand__mark { width: 52px; height: 52px; }
  .brand--small { top: 108px; font-size: 34px; gap: 12px; }
  .brand--small .brand__mark { width: 32px; height: 32px; }

  .tagline {
    position: absolute;
    top: 245px;
    left: 0; right: 0;
    text-align: center;
    font-size: 18px;
    color: var(--brand-blue);
  }

  .mission {
    position: absolute;
    top: 83px;
    left: 0; right: 0;
    text-align: center;
    font-size: 17.4px;
    line-height: 23.5px;
    color: var(--ink);
  }

  .person {
    position: absolute;
    top: 84px;
    left: 0; right: 0;
    text-align: center;
    color: var(--brand-blue);
    font-size: 19px;
  }
  .person__role { font-size: 14.5px; }

  .contacts {
    position: absolute;
    top: 137px;
    left: 0;
    width: 525px;
    font-size: 13.5px;
    color: var(--muted);
  }
  .contacts__col {
    position: absolute;
    top: 0;
    line-height: 26px;
  }
  .contacts__col--left { right: 270px; text-align: right; }
  .contacts__col--right { left: 270px; text-align: left; }
  .contacts__divider {
    position: absolute;
    left: 261px;
    top: 4px;
    width: 1px;
    height: 44px;
    background: var(--divider);
  }
  .contacts__label { color: var(--brand-blue); font-weight: bold; }

  .address {
    position: absolute;
    top: 206px;
    left: 0; right: 0;
    text-align: center;
    font-size: 13px;
    color: var(--muted);
  }
</style>
</head>
<body>
  <div class="side-label side-label--front">Front</div>
  <div class="side-label side-label--back">Back</div>

  <section class="card card--front-top">
    <div class="brand brand--large"><span class="brand__mark"></span><span class="brand__name">KORVANEX</span></div>
  </section>

  <section class="card card--front-bottom">
    <p class="mission">
      Korvanex is the leading building services innovator.<br>
      By combining technology with functional toos that<br>
      improve efficiency in the workplace, we provide<br>
      unparalleled service in the industry. Developing<br>
      lasting relationships with our clients and associates<br>
      is the cornerstone of our success.
    </p>
  </section>

  <section class="card card--back-top">
    <div class="brand brand--small"><span class="brand__mark"></span><span class="brand__name">KORVANEX</span></div>
    <p class="tagline">Where Care Finds Its Pulse</p>
  </section>

  <section class="card card--back-bottom">
    <p class="person">Your Name, <span class="person__role">Designation</span></p>
    <div class="contacts">
      <div class="contacts__col contacts__col--left">
        <div><span class="contacts__label">cell</span> : +12 345 67 8910</div>
        <div><span class="contacts__label">email</span> : info@yoursite-demo.net</div>
      </div>
      <span class="contacts__divider"></span>
      <div class="contacts__col contacts__col--right">
        <div><span class="contacts__label">phone</span> : +12 345 67 8910</div>
        <div><span class="contacts__label">web</span> : www.yoursite-demo.net</div>
      </div>
    </div>
    <p class="address">123, Abc Street, 0000 City, Country</p>
  </section>
</body>
</html>
```